Smart Design for Global Industrial Business

We are commissioned to replace an existing industrial business website with a new website with new branding and layout for CMS / Responsive (Wordpress). The existing website is to be replaced (rvtbindings.com) with one that is more in keeping with the new brand book and modern design standards.
Note that they have two online stores (rvt-gripping.co.uk and .com) and this site will need to fit with those, whilst being very different and much more about RVT and their scope / reach.
Please just design the homepage first as we will try to give everyone a chance to build from there if they are heading in the right direction.
The eventual delivery will be of all the wireframes, in source file format (ideally PSD) as well as PNGs.
We will aim to feedback in detail to all participants, but if you really don't try that hard, it may be brief!

Target Market(s)

Buyers in companies who are looking for clamping / restraining products - to persuade them that these are the best, most reliable, products.

Industry/Entity Type

Industrial safety/banding products

Number of Pages Required

5+ page

Font styles to use
Sans Serif
Other font styles liked:
• see current websites

Requirements
Must have
• A really good consistent level of design with consideration of mobile users and lead generation.
Nice to have
• I just want to see good creative, if possible. Don't try too many things, keep it simple.
Should not have
• No untidiness or lack of consistency.

```html
<!DOCTYPE html>
<html lang="en">
<head>
<meta charset="utf-8">
<title>RVT Fasteners – Clamping and Banding Solutions</title>
<link href="https://fonts.googleapis.com/css2?family=Barlow:wght@300;400;500;600;700&display=swap" rel="stylesheet">
<style>
:root{
  --orange:#e8572a;
  --navy:#1f2b3b;
  --ink:#2a3340;
  --muted:#5d6673;
  --line:#c9d3de;
  --footer:#262e3b;
  --white:#fff;
}
*{box-sizing:border-box;margin:0;padding:0}
html,body{width:1200px;height:4648px;overflow:hidden}
body{font-family:"Barlow",sans-serif;color:var(--ink);background:#fff;position:relative}
a{color:inherit;text-decoration:none}
.abs{position:absolute}
.bar{display:block;width:76px;height:4px;background:var(--orange)}

/* header */
.topbar{position:absolute;top:0;left:0;width:1200px;height:26px;border-bottom:1px solid #eceff3;font-size:11px;font-weight:600;color:var(--navy)}
.topbar nav{position:absolute;right:50px;top:8px;display:flex;gap:30px}
.header{position:absolute;top:26px;left:0;width:1200px;height:93px;background:#fff}
.brand{position:absolute;left:110px;top:22px;display:flex;align-items:center;gap:10px;font-weight:700;font-size:40px;color:var(--navy);letter-spacing:1px}
.brand i{display:block;width:14px;height:14px;border-radius:50%;background:var(--orange)}
.mainnav{position:absolute;left:322px;top:0;display:flex;gap:44px;height:93px;align-items:center;font-size:14px;font-weight:500;color:#6b7480}
.mainnav a{position:relative;height:93px;line-height:93px}
.mainnav a.active{color:var(--navy);font-weight:600}
.mainnav a.active::after{content:"";position:absolute;left:0;right:0;bottom:0;height:4px;background:var(--orange)}

/* hero */
.hero{position:absolute;top:119px;left:0;width:1200px;height:627px;background:linear-gradient(160deg,#5b6f72 0%,#2b3d52 35%,#1c2b44 65%,#16223a 100%)}
.hero .kicker{position:absolute;left:107px;top:200px;color:#fff;font-size:25px;font-weight:400;letter-spacing:5px}
.hero h1{position:absolute;left:107px;top:232px;color:#fff;font-size:46px;line-height:51px;font-weight:700}
.hero .bar{position:absolute;left:110px;top:347px;width:82px}
.tabs{position:absolute;left:112px;top:388px;display:flex;gap:2px}
.tabs span{width:255px;height:53px;line-height:53px;text-align:center;background:#243349;color:#fff;font-size:16px;font-weight:600}
.tabs span b{font-weight:300;margin-right:6px}
.tabs span.on{background:var(--orange)}
.arrow{position:absolute;top:250px}

/* intro */
.intro{position:absolute;top:746px;left:0;width:1200px;height:509px;background:#fff}
.introbox{position:absolute;left:121px;top:91px;width:955px;height:346px;border:2px solid var(--line)}
.introbox .brand{left:66px;top:-30px;background:#fff;padding:0 16px;font-size:36px}
.introbox .col{position:absolute;top:76px;width:390px;font-size:14px;line-height:22px;color:var(--muted)}
.introbox .col p+p{margin-top:22px}
.introbox .divide{position:absolute;left:482px;top:76px;width:1px;height:200px;background:var(--line)}

/* water */
.water{position:absolute;top:1255px;left:0;width:1200px;height:500px;background:linear-gradient(180deg,#b8c8d8 0%,#d4dfe9 40%,#c6d3e0 100%)}
.water h2{position:absolute;left:114px;top:116px;font-size:33px;line-height:37px;font-weight:700;color:var(--navy)}
.water h2 span{font-weight:400}
.select{position:absolute;left:119px;top:297px;width:327px;height:48px;background:#fff;border:1px solid #dde3ea;font-size:14px;line-height:48px;padding-left:22px;color:var(--ink)}
.select svg{position:absolute;right:16px;top:18px}
.water .vline{position:absolute;left:574px;top:117px;width:2px;height:228px;background:#8e9fb2}
.water .txt{position:absolute;left:635px;top:138px;width:410px;font-size:14px;line-height:21px;color:var(--muted)}
.water .txt p+p{margin-top:18px}

/* custom */
.custom{position:absolute;top:1755px;left:0;width:1200px;height:516px;background:linear-gradient(180deg,#2c3d54 0%,#223248 50%,#1a2a40 100%);color:#fff}
.custom h2{position:absolute;left:117px;top:118px;font-size:38px;line-height:36px;font-weight:700}
.custom h2 span{font-weight:300}
.custom .l{position:absolute;left:117px;top:232px;width:330px;font-size:14px;line-height:21px}
.btn{position:absolute;left:121px;top:346px;width:184px;height:43px;border:2px solid #fff;font-size:14px;font-weight:600;line-height:39px;text-align:center}
.custom .r{position:absolute;left:635px;top:232px;width:440px;font-size:14px;line-height:21px}
.custom .r u{text-underline-offset:2px}
.custom .r p+p{margin-top:10px}

/* case studies */
.cases{position:absolute;top:2271px;left:0;width:1200px;height:774px;background:#fff}
.sechead{position:absolute;left:112px;font-size:30px;line-height:34px;font-weight:700;color:var(--navy)}
.sechead span{font-weight:400}
.cases .sechead{top:58px}
.cases .bar{position:absolute;left:114px;top:137px}
.case{position:absolute;width:477px;height:241px;background:linear-gradient(180deg,#5e7390,#2a3a52)}
.case .cap{position:absolute;left:0;right:0;bottom:0;height:56px;background:rgba(40,50,64,.72);color:#fff;font-size:17px;font-weight:700;line-height:56px;padding-left:28px}
.case .cap.hot{background:rgba(232,87,42,.92)}
.accent-tl{position:absolute;left:108px;top:2452px;width:88px;height:8px;background:var(--orange)}
.accent-tl2{position:absolute;left:108px;top:2452px;width:8px;height:100px;background:var(--orange)}
.accent-br{position:absolute;left:1005px;top:2960px;width:90px;height:8px;background:var(--orange)}
.accent-br2{position:absolute;left:1087px;top:2868px;width:8px;height:100px;background:var(--orange)}

/* news */
.news{position:absolute;top:3045px;left:0;width:1200px;height:524px;background:#f1f4f7}
.news .sechead{top:62px;font-size:28px}
.news .bar{position:absolute;left:112px;top:96px;width:66px}
.card{position:absolute;top:126px;width:236px;height:316px;background:#fff;border:1px solid #cfd6de}
.card .pic{height:160px;position:relative}
.card .date{position:absolute;left:4px;bottom:0;background:var(--orange);color:#fff;font-size:10px;font-weight:600;padding:3px 8px}
.card h3{margin:26px 20px 0;font-size:12px;line-height:15px;font-weight:700;color:var(--navy)}
.card p{margin:6px 20px 0;font-size:10px;color:var(--muted)}
.card .more{position:absolute;left:20px;bottom:40px;font-size:11px;font-weight:700;color:var(--orange)}

/* offices */
.offices{position:absolute;top:3569px;left:0;width:1200px;height:703px;background:#fff}
.office{position:absolute;top:57px;width:482px;height:547px;border:1px solid #d9dfe6;background:#fff}
.office .map{height:262px;background:linear-gradient(135deg,#eceff2,#dfe3e8)}
.office .pin{position:absolute}
.office h3{position:absolute;left:42px;top:290px;font-size:20px;line-height:24px;font-weight:700;color:var(--navy);border-left:3px solid var(--orange);padding-left:12px}
.office h3 span{display:block;font-weight:400}
.office .lbl{position:absolute;left:42px;font-size:14px;font-weight:700;color:var(--navy)}
.office .addr{position:absolute;left:42px;font-size:12.5px;line-height:23px;color:var(--muted)}
.office .row{display:flex;gap:8px;align-items:flex-start}
.office .row svg{margin-top:4px;flex:none}
.office .corner{position:absolute;right:-6px;bottom:-6px;width:86px;height:6px;background:var(--orange)}
.office .corner2{position:absolute;right:-6px;bottom:-6px;width:6px;height:100px;background:var(--orange)}

/* footer */
.footer{position:absolute;top:4272px;left:0;width:1200px;height:309px;background:var(--footer);color:#c4cbd6}
.fcol{position:absolute;top:62px;border-left:4px solid var(--orange);padding-left:24px;height:36px}
.fcol::before{content:"";position:absolute;left:-4px;top:-60px;width:1px;height:250px;background:#3a4352}
.fcol h4{color:#fff;font-size:16px;font-weight:600;line-height:36px}
.fcol ul{list-style:none;margin-top:12px;font-size:11px;line-height:23px}
.fcol ul b{color:#fff;font-weight:600}
.fcol ul u{text-underline-offset:2px}
.social{position:absolute;left:892px;top:243px;display:flex;gap:28px}
.social i{display:block;width:16px;height:16px;border-radius:50%;background:#fff}
.legal{position:absolute;top:4581px;left:0;width:1200px;height:67px;background:var(--orange);color:#fff;font-size:11px}
.legal .c{position:absolute;left:130px;top:27px;opacity:.6}
.legal nav{position:absolute;right:138px;top:27px;display:flex;gap:14px}
</style>
</head>
<body>

<div class="topbar"><nav><a>NEWS</a><a>ABOUT US</a><a>CONTACT US</a></nav></div>
<header class="header">
  <a class="brand">RVT<i></i></a>
  <nav class="mainnav">
    <a class="active">HOSE CLAMPS</a><a>BANDINGS &amp; SADDLES</a><a>CUSTOM SOLUTIONS</a><a>APPLICATIONS</a><a>CASE STUDIES</a>
  </nav>
</header>

<section class="hero" role="img" aria-label="Photo of large pipelines wrapped with banding at a waterside site">
  <svg class="arrow" style="left:32px" width="26" height="54" viewBox="0 0 26 54"><path d="M24 2 2 27l22 25" fill="none" stroke="#fff" stroke-width="2"/></svg>
  <svg class="arrow" style="left:1132px" width="26" height="54" viewBox="0 0 26 54"><path d="m2 2 22 25L2 52" fill="none" stroke="#fff" stroke-width="2"/></svg>
  <div class="kicker">THE LEADING MANUFACTURING</div>
  <h1>AND SUPPLIER OF CLAMPING<br>AND BANDING SOLUTIONS</h1>
  <span class="bar"></span>
  <div class="tabs">
    <span><b>01</b>HOSE CLAMPS</span>
    <span class="on"><b>02</b>BANDING</span>
    <span><b>03</b>CUSTOM SOLUTIONS</span>
  </div>
</section>

<section class="intro">
  <div class="introbox">
    <a class="brand">RVT<i></i></a>
    <div class="col" style="left:59px">
      <p>RVT Fasteners is one of the world's leading producers and suppliers of clamping systems for commercial and personal use. We manufacture of non-metallic smart polymer hose clamps and clips - including Bramble Clip, Tidyclamp, Tidyclik and a range of tools.</p>
      <p>We also supply a wide range of selected high quality distributed brands from the most recognised and respected brands of hose clamps and clips.</p>
    </div>
    <div class="divide"></div>
    <div class="col" style="left:525px">
      <p>With warehouses in the US and the UK we are now supplying across the world both standard and custom solutions to deliver long-lasting, reliable and secure clamping and banding solutions.</p>
      <p>So, please browse our website or contact us if you have a specific requirement, we look forward to hearing from you.</p>
    </div>
  </div>
</section>

<section class="water" role="img" aria-label="Photo of a floating pipeline in a calm bay">
  <h2>WATER. SUN.<br>COLD. SALT. WIND<br><span>WE'VE GOT IT COVERED</span></h2>
  <div class="select">Choose a Challenge?
    <svg width="16" height="10" viewBox="0 0 16 10"><path d="m1 1 7 7 7-7" fill="none" stroke="#4a5462" stroke-width="2"/></svg>
  </div>
  <div class="vline"></div>
  <div class="txt">
    <p>There are many situations where you need the right solution to make sure that whatever you need to secure is fixed for good</p>
    <p>At RVT our aim is to recommend the best product for your specific situation, regardless of whether it is ours, or another company. So select your challenge, and explore the best product(s) to suit your needs.</p>
  </div>
</section>

<section class="custom" role="img" aria-label="Photo of pier pilings over dark water">
  <h2>CUSTOM<br><span>SOLUTIONS</span></h2>
  <p class="l">Our specialisation in non-metallic polymer hose clamps, clips and branding means that we supply to specific projects around the world. Discover how we may be able to assist you.</p>
  <a class="btn">FIND OUT MORE &rsaquo;</a>
  <div class="r">
    <p>Or, if you prefer, <u>contact our sales team.</u></p>
    <p>They are experienced in helping understand your requirements, and will bring together a full proposal for exactly what you need. This may include any specialist tools and recommendations on installation partners needed to fulfil the project.</p>
  </div>
</section>

<section class="cases">
  <h2 class="sechead">CASE STUDIES<br><span>RVT PRODUCT IN PLACE</span></h2>
  <span class="bar"></span>
</section>
<div class="accent-tl"></div><div class="accent-tl2"></div>
<div class="case" style="left:116px;top:2460px" role="img" aria-label="Photo of pile wrap system on pier columns"><div class="cap hot">PILE WRAP SYSTEM THORNLEA</div></div>
<div class="case" style="left:608px;top:2460px;background:linear-gradient(180deg,#8592a0,#3b4654)" role="img" aria-label="Photo of subsea cable attachments on a long cable"><div class="cap">SUBSEA CABLE ATTACHMENT - MARENDO</div></div>
<div class="case" style="left:116px;top:2720px;background:linear-gradient(180deg,#5d7a8c,#3e4c44)" role="img" aria-label="Photo of a clamped piling beside a work lift"><div class="cap">ICCP COLD HORBOUR</div></div>
<div class="case" style="left:610px;top:2720px;background:linear-gradient(180deg,#6b6f74,#3a3f46)" role="img" aria-label="Photo of downhole equipment on a work site"><div class="cap">DOWNHOLE - COLUMBIA</div></div>
<div class="accent-br"></div><div class="accent-br2"></div>

<section class="news">
  <h2 class="sechead">NEWS, EVENTS <span>&amp; FEATURES</span></h2>
  <span class="bar"></span>
  <article class="card" style="left:112px">
    <div class="pic" role="img" aria-label="Photo of an exhibition stand" style="background:linear-gradient(180deg,#3d5a9a,#1f3366)"><span class="date">JULY 20, 2021</span></div>
    <h3>WE ATTENDED THE MARITIME 2021 CONFERENCE</h3><p>Lorem ipsum dolor sit amet consect</p><a class="more">LEARN MORE &rarr;</a>
  </article>
  <article class="card" style="left:361px">
    <div class="pic" role="img" aria-label="Video still of an installation on site" style="background:linear-gradient(180deg,#7b6e62,#3d3a38)"><span class="date">JULY 20, 2021</span></div>
    <h3>RECENT INSTALLATION IN SAUDI ARABIA</h3><p>Lorem ipsum dolor sit amet, consect</p><a class="more">LEARN MORE &rarr;</a>
  </article>
  <article class="card" style="left:612px">
    <div class="pic" role="img" aria-label="Photo of product testing rig" style="background:linear-gradient(180deg,#8a8c8e,#4d4f52)"><span class="date">JULY 20, 2021</span></div>
    <h3>TESTING OUR PRODUCTS, HOW WE MAKE SURE THAT RVT SOLUTIONS ARE FIT FOR PURPOSE</h3><a class="more">LEARN MORE &rarr;</a>
  </article>
  <article class="card" style="left:861px">
    <div class="pic" role="img" aria-label="Photo of a banding tool" style="background:linear-gradient(180deg,#f2f2f2,#c9c9c9)"><span class="date">JULY 20, 2021</span></div>
    <h3>CUSTOM TOOLS - WHEN YOU NEED TO MAKE SURE THE FIT IS RIGHT</h3><a class="more">LEARN MORE &rarr;</a>
  </article>
</section>

<section class="offices">
  <div class="office" style="left:99px">
    <div class="map" role="img" aria-label="Street map of the UK office location"></div>
    <svg class="pin" style="left:215px;top:140px" width="26" height="36" viewBox="0 0 26 36"><path d="M13 35C5 23 1 18 1 12a12 12 0 0 1 24 0c0 6-4 11-12 23z" fill="#2a3446"/><circle cx="13" cy="12" r="4.5" fill="#fff"/></svg>
    <h3>RVT FASTENERS LIMITED<span>FOR UK, EU, EMEA &amp; WORLDWIDE</span></h3>
    <div class="lbl" style="top:378px">MAIN OFFICE:</div>
    <div class="addr" style="top:398px">Gripping House
      <div class="row"><svg width="14" height="18" viewBox="0 0 26 36"><path d="M13 35C5 23 1 18 1 12a12 12 0 0 1 24 0c0 6-4 11-12 23z" fill="#e8572a"/><circle cx="13" cy="12" r="4.5" fill="#fff"/></svg><span>2nd Avenue Northfield Trading Estate<br>Midford, Bath, Somerset BA3 9ZZ<br>United Kingdom</span></div>
      <div class="row"><svg width="14" height="14" viewBox="0 0 24 24"><path d="M6.6 10.8a15 15 0 0 0 6.6 6.6l2.2-2.2a1 1 0 0 1 1-.25 11 11 0 0 0 3.6.6 1 1 0 0 1 1 1V20a1 1 0 0 1-1 1A17 17 0 0 1 3 4a1 1 0 0 1 1-1h3.5a1 1 0 0 1 1 1c0 1.25.2 2.45.6 3.6a1 1 0 0 1-.25 1z" fill="#e8572a"/></svg><span>Tel: +44 (0)1632 960418</span></div>
    </div>
    <div class="corner"></div><div class="corner2"></div>
  </div>
  <div class="office" style="left:612px">
    <div class="map" role="img" aria-label="Street map of the US office location"></div>
    <svg class="pin" style="left:215px;top:100px" width="26" height="36" viewBox="0 0 26 36"><path d="M13 35C5 23 1 18 1 12a12 12 0 0 1 24 0c0 6-4 11-12 23z" fill="#2a3446"/><circle cx="13" cy="12" r="4.5" fill="#fff"/></svg>
    <h3 style="top:286px">RVT FASTENERS CORP<span>FOR USA &amp; CANADA</span></h3>
    <div class="lbl" style="top:370px">MAIN OFFICE:</div>
    <div class="addr" style="top:398px">
      <div class="row"><svg width="14" height="18" viewBox="0 0 26 36"><path d="M13 35C5 23 1 18 1 12a12 12 0 0 1 24 0c0 6-4 11-12 23z" fill="#e8572a"/><circle cx="13" cy="12" r="4.5" fill="#fff"/></svg><span>Parkway 1990 Business Centre<br>18400 Parkway Road, Suite 12<br>Houston, Texas, 77064 USA</span></div>
      <div class="row" style="margin-top:4px"><svg width="14" height="14" viewBox="0 0 24 24"><path d="M6.6 10.8a15 15 0 0 0 6.6 6.6l2.2-2.2a1 1 0 0 1 1-.25 11 11 0 0 0 3.6.6 1 1 0 0 1 1 1V20a1 1 0 0 1-1 1A17 17 0 0 1 3 4a1 1 0 0 1 1-1h3.5a1 1 0 0 1 1 1c0 1.25.2 2.45.6 3.6a1 1 0 0 1-.25 1z" fill="#e8572a"/></svg><span>Tel: 281 555 0142</span></div>
      <div class="row" style="margin-top:4px"><svg width="14" height="14" viewBox="0 0 24 24"><path d="M6.6 10.8a15 15 0 0 0 6.6 6.6l2.2-2.2a1 1 0 0 1 1-.25 11 11 0 0 0 3.6.6 1 1 0 0 1 1 1V20a1 1 0 0 1-1 1A17 17 0 0 1 3 4a1 1 0 0 1 1-1h3.5a1 1 0 0 1 1 1c0 1.25.2 2.45.6 3.6a1 1 0 0 1-.25 1z" fill="#e8572a"/></svg><span>Toll free: 1-866 555 0199</span></div>
    </div>
    <div class="corner"></div><div class="corner2"></div>
  </div>
</section>

<footer class="footer">
  <div class="fcol" style="left:135px"><h4>HOSE CLAMPS</h4><ul><li>Bramble Clips</li><li>Tidyclamp</li><li>Tidyclik</li><li>Air Tools</li><li>Distributed Brands</li></ul></div>
  <div class="fcol" style="left:389px"><h4>HOSE CLAMPS</h4><ul><li>Smart Band</li><li>Smart Tie</li><li>Smart Protectors</li><li>Smart Saddles</li><li>Installation Tools</li></ul></div>
  <div class="fcol" style="left:624px"><h4>HOSE CLAMPS</h4><ul><li>Custom Solutions</li><li>Applications</li><li>Case Studies</li><li>Quality &amp; Testing</li><li>Facility</li><li>Contact Us</li></ul></div>
  <div class="fcol" style="left:857px"><h4>CONTACT RVT</h4><ul style="line-height:19px"><li><u>Send an Email</u></li><li><b>UK/EU</b></li><li>Tel: +44 (0)1632 960418</li><li>Online Store</li><li><b>US/CA</b></li><li>Tel: 281 555 0142</li><li>Toll free: 1-866 555 0199</li></ul></div>
  <div class="social"><i></i><i></i><i></i></div>
</footer>
<div class="legal">
  <span class="c">© RVT Fasteners Limited. All rights reserved</span>
  <nav><a>Sitemap</a><a>Terms of Use</a><a>Privacy Policy</a><a>Contact Us</a></nav>
</div>

</body>
</html>
```